Business card for my new company (Accounting firm)

I need a business card for my new business Brightwell Advisory and Ledger SA. Our services are accounting, tax, audit and financial management. Our customers are small companies, start-ups and new companies. The final design has to show financial security, trust and growth. Please find our logo attached to the business card. Text for the business card: Brightwell Advisory and Ledger SA Tomas Varenholt Director and Founder Certified Accountant Tel. 022 418 57 34 tv@clairevalconseil.ch www.clairevalconseil.ch Rue des Vergières 27 1201 Geneva
Target Market(s)
Our customers are small companies, start-ups and new companies.
Industry/Entity Type
Finance And Accounting
Contact Information for Business Card
Claireval Conseil et Comptes SA
Tomas Varenholt
Directeur et Fondateur
Expert-comptable diplômé
Tél. 022 418 57 34
tv@clairevalconseil.ch
www.clairevalconseil.ch
Rue des Vergières 27
1201 Genève

```html
<!DOCTYPE html>
<html lang="fr">
<head>
<meta charset="utf-8">
<title>Claireval Conseil et Comptes SA – Carte de visite</title>
<link rel="stylesheet" href="https://fonts.googleapis.com/css2?family=Lato:wght@400;700&display=swap">
<style>
  :root {
    --backdrop: #141516;
    --card: #1d1e20;
    --ink: #ffffff;
    --ink-soft: #e6e8ea;
    --accent: #2a8fd6;
    --accent-light: #35aee6;
  }
  * { box-sizing: border-box; margin: 0; padding: 0; }
  html, body {
    width: 1200px;
    height: 912px;
    overflow: hidden;
    background: var(--backdrop);
    font-family: "Lato", Arial, sans-serif;
  }
  .sheet {
    width: 1200px;
    height: 912px;
    display: flex;
    flex-direction: column;
    align-items: center;
    justify-content: center;
    gap: 40px;
  }
  .card {
    width: 700px;
    height: 400px;
    background: var(--card);
    position: relative;
    display: flex;
    align-items: center;
  }

  /* Wordmark */
  .wordmark {
    display: flex;
    align-items: center;
    gap: 16px;
    color: var(--ink);
    font-weight: 700;
  }
  .wordmark__square {
    width: 34px;
    height: 34px;
    background: var(--accent);
    flex: none;
  }
  .wordmark__text { display: flex; flex-direction: column; line-height: 1; }
  .wordmark__name { font-size: 52px; letter-spacing: 2px; }
  .wordmark__sub  { font-size: 15px; letter-spacing: 3.2px; margin-top: 8px; }

  /* Front */
  .card--front { justify-content: center; }

  /* Back */
  .card--back { padding-left: 56px; }
  .card--back .wordmark__name { font-size: 40px; }
  .card--back .wordmark__sub  { font-size: 11.5px; letter-spacing: 2.4px; }
  .card--back .wordmark__square { width: 26px; height: 26px; }
  .divider {
    width: 2px;
    height: 220px;
    background: var(--accent);
    margin: 0 34px 0 40px;
  }
  .details { color: var(--ink-soft); font-size: 15px; line-height: 1.3; }
  .details__name {
    color: var(--accent);
    font-weight: 700;
    font-size: 23px;
    margin-bottom: 4px;
  }
  .details__block { margin-bottom: 12px; }
  .contact { list-style: none; }
  .contact li { display: flex; align-items: center; gap: 10px; }
  .contact svg { width: 14px; height: 14px; fill: var(--accent); flex: none; }
</style>
</head>
<body>
<main class="sheet">

  <section class="card card--front" aria-label="Recto">
    <div class="wordmark">
      <span class="wordmark__square"></span>
      <div class="wordmark__text">
        <span class="wordmark__name">CLAIREVAL</span>
        <span class="wordmark__sub">CONSEIL ET COMPTES</span>
      </div>
    </div>
  </section>

  <section class="card card--back" aria-label="Verso">
    <div class="wordmark">
      <span class="wordmark__square"></span>
      <div class="wordmark__text">
        <span class="wordmark__name">CLAIREVAL</span>
        <span class="wordmark__sub">CONSEIL ET COMPTES</span>
      </div>
    </div>

    <div class="divider"></div>

    <div class="details">
      <p class="details__name">Tomas Varenholt</p>
      <div class="details__block">
        <p>Directeur et Fondateur</p>
        <p>Expert-comptable diplômé</p>
      </div>
      <div class="details__block">
        <p>Claireval Conseil et Comptes SA</p>
        <p>Rue des Vergières 27</p>
        <p>1201 Genève</p>
      </div>
      <ul class="contact">
        <li>
          <svg viewBox="0 0 24 24" aria-hidden="true"><path d="M6.6 10.8a15 15 0 0 0 6.6 6.6l2.2-2.2a1 1 0 0 1 1-.25 11.4 11.4 0 0 0 3.6.57 1 1 0 0 1 1 1V20a1 1 0 0 1-1 1A17 17 0 0 1 3 4a1 1 0 0 1 1-1h3.5a1 1 0 0 1 1 1c0 1.25.2 2.45.57 3.57a1 1 0 0 1-.25 1z"/></svg>
          022 418 57 34
        </li>
        <li>
          <svg viewBox="0 0 24 24" aria-hidden="true"><path d="M2 5h20v14H2z M2 5l10 8 10-8" fill="none" stroke="var(--accent)" stroke-width="2"/><path d="M2 5h20l-10 8z"/></svg>
          tv@clairevalconseil.ch
        </li>
        <li>
          <svg viewBox="0 0 24 24" aria-hidden="true"><circle cx="12" cy="12" r="9" fill="none" stroke="var(--accent)" stroke-width="2"/><path d="M3 12h18M12 3c3 3 3 15 0 18M12 3c-3 3-3 15 0 18" fill="none" stroke="var(--accent)" stroke-width="1.6"/></svg>
          www.clairevalconseil.ch
        </li>
      </ul>
    </div>
  </section>

</main>
</body>
</html>
```